Business Card Design

We need a business card designed for our new company. Prefer a black card with white logo & writing.

Contact Information for Business Card

Ted Galloway, address: 7-4812 Fernhollow Road, Abbotsford, BC, V3K 8R2, Office Phone: 604-712-3390, Cell: 604-947-2164, Email: ted@resinworkshub.ca

Colors

Designer to choose only greyscale colors for use in the design.

```html
<!DOCTYPE html>
<html lang="en">
<head>
<meta charset="utf-8">
<title>Resinworks Hub – Business Card</title>
<link href="https://fonts.googleapis.com/css2?family=Poppins:wght@300;400;700&display=swap" rel="stylesheet">
<style>
  :root {
    --backdrop: #1e1e1f;
    --card: #232326;
    --card-pattern-light: #2e2e32;
    --card-pattern-dark: #1b1b1e;
    --ink: #ffffff;
    --ink-soft: #d9d9d9;
    --rule: #bdbdbd;
  }
  * { box-sizing: border-box; margin: 0; padding: 0; }
  html, body {
    width: 1200px; height: 711px; overflow: hidden;
    background: var(--backdrop);
    font-family: "Poppins", sans-serif;
    color: var(--ink);
  }
  .stage {
    position: relative; width: 1200px; height: 711px;
    display: flex; align-items: center; justify-content: center; gap: 60px;
  }
  .card {
    position: relative; width: 520px; height: 297px;
    background: var(--card);
    border-radius: 4px;
    box-shadow: 0 14px 30px rgba(0,0,0,.55);
    overflow: hidden;
  }
  .card-back__pattern {
    position: absolute; inset: 0;
    background: linear-gradient(135deg, var(--card-pattern-light) 0%, var(--card) 45%, var(--card-pattern-dark) 100%);
  }
  .brand {
    position: absolute; left: 36px; top: 110px; width: 190px;
    display: flex; align-items: center; gap: 10px;
  }
  .brand__mark {
    width: 14px; height: 14px; border: 2px solid var(--ink); flex: none;
  }
  .brand__name {
    font-weight: 700; font-size: 22px; line-height: 1.05;
    letter-spacing: .5px; text-transform: uppercase;
  }
  .divider {
    position: absolute; left: 246px; top: 96px; width: 1px; height: 116px;
    background: var(--rule); transform: rotate(-18deg); transform-origin: top;
  }
  .person { position: absolute; left: 300px; top: 62px; }
  .person__name { font-size: 25px; line-height: 1; }
  .person__first { font-weight: 700; }
  .person__last { font-weight: 300; }
  .person__role { font-size: 11px; font-weight: 400; margin-top: 4px; color: var(--ink-soft); }
  .contacts { position: absolute; left: 300px; top: 126px; list-style: none; }
  .contacts li {
    display: flex; align-items: center; gap: 9px;
    font-size: 11.5px; font-weight: 300; height: 20px;
  }
  .contacts svg { width: 12px; height: 12px; flex: none; }
  .address {
    position: absolute; left: 0; right: 0; bottom: 26px; text-align: center;
    font-size: 12.5px; font-weight: 400;
  }
</style>
</head>
<body>
<main class="stage">
  <section class="card card-back">
    <div class="card-back__pattern" role="img" aria-label="Repeating brand pattern in tonal dark grey across the card back"></div>
  </section>

  <section class="card card-front">
    <div class="brand">
      <span class="brand__mark"></span>
      <span class="brand__name">Resinworks Hub</span>
    </div>
    <span class="divider"></span>
    <div class="person">
      <p class="person__name"><span class="person__first">Ted</span> <span class="person__last">Galloway</span></p>
      <p class="person__role">Founder &amp; CEO</p>
    </div>
    <ul class="contacts">
      <li>
        <svg viewBox="0 0 24 24" fill="none" stroke="currentColor" stroke-width="2"><path d="M5 3h4l2 5-3 2a11 11 0 0 0 6 6l2-3 5 2v4a2 2 0 0 1-2 2A17 17 0 0 1 3 5a2 2 0 0 1 2-2z"/></svg>
        604-712-3390
      </li>
      <li>
        <svg viewBox="0 0 24 24" fill="none" stroke="currentColor" stroke-width="2"><rect x="6" y="2" width="12" height="20" rx="2"/><line x1="11" y1="18" x2="13" y2="18"/></svg>
        604-947-2164
      </li>
      <li>
        <svg viewBox="0 0 24 24" fill="none" stroke="currentColor" stroke-width="2"><circle cx="12" cy="12" r="10"/><path d="M2 12h20M12 2a15 15 0 0 1 0 20M12 2a15 15 0 0 0 0 20"/></svg>
        www.resinworkshub.ca
      </li>
      <li>
        <svg viewBox="0 0 24 24" fill="none" stroke="currentColor" stroke-width="2"><rect x="2" y="5" width="20" height="14" rx="1"/><path d="M2 6l10 7 10-7"/></svg>
        ted@resinworkshub.ca
      </li>
    </ul>
    <p class="address">7-4812 Fernhollow Road, Abbotsford, BC, V3K 8R2.</p>
  </section>
</main>
</body>
</html>
```